Website for a company offering full serivce charging solutions for electric cars

The company "tanu-werk" (english: "tanu-works") offering all-in-one-solutions for charging infrastructure for electric mobility.

There are four products:
1- Wallboxes for single-family homes
2- Solutions for property devloper/-management for property parking space
3- All-in-one-charging solution for municipalities/communities
4- Solutions for tourism/hotels/holiday appartments

The Website structure:
1. Main Page
2.1. Product Page Single Homes
2.2. Product Page Property Management / Parking
2.3. Product Page Municipality
2.4. Product Page Tourism
3. Contact Form / Request for information
4. Imprint / Legal

The Website should be built on Wordpress with a powerful possibility to simply add/modify specific landing pages.

We would like you to implement the website later and also maintain it if possible, but we would be able to do minor modifications by ourselfs (for A/B-Testing)

The website should be clear and simple, easy to understand.
Target group is mainly B2C without deeper knowledge of that topic.

It should suggest, that we will provide a very simple way to get the charging infrastructure done.

We need a contact form, maybe we will use Hubspot later.

Attached you will find a draft of the main page and a landing page (for 2.2) - it is just the content, please ignore the design. We would love to let you create a suitable design.
Also you will find some drafts a bit different for the same story.

I added also a few stock photos, but they don't need to be used! If you have better ideas, you are welcome!

Industry/Entity Type

Charging/Electric mobility

Number of Pages Required

2 page

Font styles to use
Sans Serif

Requirements
Must have
• Based on Wordpress, and the designer should be able to implement it on Wordpress on a later step

```html
<!DOCTYPE html>
<html lang="de">
<head>
<meta charset="utf-8">
<title>tanu-werk – Lösungen</title>
<link href="https://fonts.googleapis.com/css2?family=Catamaran:wght@700;800&family=Raleway:wght@400;500;700&family=Open+Sans:wght@400&display=swap" rel="stylesheet">
<style>
:root{
  --navy:#0a1435;
  --navy-deep:#060b1f;
  --card:#070c22;
  --footer:#111726;
  --magenta:#e112c9;
  --violet:#8a2be2;
  --white:#ffffff;
  --text:#eef0f8;
}
*{box-sizing:border-box;margin:0;padding:0}
html,body{width:794px;height:1200px;overflow:hidden}
body{position:relative;background:var(--navy);font-family:"Raleway",sans-serif;color:var(--text)}
.hero-backdrop{position:absolute;left:0;top:0;width:794px;height:536px;
  background:radial-gradient(ellipse at 70% 35%,#27408c 0%,#142463 35%,#0a1435 70%),linear-gradient(180deg,#08102c,#0b1848);}
.hero-backdrop::after{content:"";position:absolute;inset:0;background:linear-gradient(90deg,rgba(5,9,30,.55),rgba(5,9,30,.1) 60%,rgba(40,60,170,.25))}
.site-header{position:absolute;left:0;top:0;width:794px;height:100px}
.brand{position:absolute;left:94px;top:50px;white-space:nowrap}
.brand-name{font-family:"Raleway",sans-serif;font-weight:500;font-size:20px;line-height:24px;color:var(--white);letter-spacing:.2px}
.main-nav{position:absolute;top:62px;left:0;width:794px}
.main-nav a{position:absolute;font-weight:700;font-size:9.2px;color:var(--white);text-decoration:none;letter-spacing:.2px;white-space:nowrap}
.main-nav a.is-active::after{content:"";position:absolute;left:-1px;right:-2px;top:16px;height:1.5px;background:var(--magenta)}
.hero-content{position:absolute;left:95px;top:150px;width:600px}
.hero-title{font-family:"Catamaran",sans-serif;font-weight:800;font-size:32px;line-height:36px;color:var(--magenta)}
.hero-lead{font-family:"Raleway",sans-serif;font-weight:700;font-size:15px;line-height:21.5px;color:var(--white);margin-top:21px}
.hero-text{font-size:10.4px;line-height:16px;color:var(--white);margin-top:24px}
.hero-text .hl{color:var(--magenta)}
.offer{position:absolute;background:var(--card);width:257px}
.offer-photo{position:absolute;left:12px;width:234px;height:107px}
.offer-banner{position:absolute;left:12px;width:234px;height:30px;display:flex;align-items:center;justify-content:center;
  font-family:"Catamaran",sans-serif;font-weight:800;font-size:14px;color:var(--white);background:var(--magenta)}
.offer-banner.is-business{background:var(--violet)}
.offer-list{position:absolute;left:12px;width:240px;list-style:none}
.offer-list li{position:relative;padding-left:22px;font-size:8.4px;line-height:15.9px;color:var(--white)}
.offer-list li svg{position:absolute;left:0;top:4px;width:9px;height:8px}
.offer-list li.sub{padding-left:40px}
.offer-list li.sub::before{content:"-";position:absolute;left:35px;color:#9aa}
.site-footer{position:absolute;left:0;top:1063px;width:794px;height:137px;background:var(--footer);font-family:"Open Sans",sans-serif}
.site-footer a,.site-footer span{position:absolute;top:58px;font-size:9.8px;color:var(--white);text-decoration:none;white-space:nowrap}
.social{position:absolute;top:91px;width:20px;height:20px;border-radius:50%;background:#3a3f4c}
</style>
</head>
<body>
<div class="hero-backdrop" role="img" aria-label="Abgedunkeltes Foto eines Elektroautos an einer Ladesäule in blauem Licht"></div>

<header class="site-header">
  <div class="brand">
    <div class="brand-name">tanu-werk.de</div>
  </div>
  <nav class="main-nav">
    <a class="is-active" style="left:318px">LÖSUNGEN</a>
    <a style="left:400px">UNTERNEHMEN</a>
    <a style="left:503px">SERVICES</a>
    <a style="left:578px">KARRIERE</a>
    <a style="left:654px">KONTAKT</a>
  </nav>
</header>

<section class="hero-content">
  <h1 class="hero-title">TANU-WERK IST<br>IHR PARTNER</h1>
  <h2 class="hero-lead">Wenn das Laden nicht nur einfach,<br>sondern die Umsetzung auch aus einer<br>Hand kommen soll</h2>
  <p class="hero-text">Wir&nbsp; bieten Lösungen sowohl für <span class="hl">Privatkunden, Geschäftskunden</span> als auch <span class="hl">Kommunen</span> an, die schnell,<br>fair und ohne Eigenleistung zu einer smarten Ladelösung für E-Fahrzeuge kommen möchten.</p>
  <p class="hero-text" style="margin-top:21px">Von der Beratung, über die Installation, Inbetriebnahme bis zur Abrechnung und Wartung bekommen Sie bei<br>tanu-werk alles aus einer Hand. Auf Wunsch vermieten wir auch die Ladetechnik und übernehmen im gewerblichen<br>Bereich die direkte Abrechnung mit dem Nutzer. Für Kommunen bieten wir den kostenfreien Full-Service an und<br>beteiligen die Gemeinden an der Nutzung der Infrastruktur.</p>
  <p class="hero-text" style="margin-top:16px">Fragen Sie uns nach der auf Ihre individuellen Bedürfnisse zugeschnittenen Lösung:</p>
</section>

<svg width="0" height="0" style="position:absolute">
  <symbol id="tick" viewBox="0 0 10 8"><path d="M1 4.2 3.8 7 9 1" fill="none" stroke="#e112c9" stroke-width="2" stroke-linecap="round" stroke-linejoin="round"/></symbol>
</svg>

<article class="offer" style="left:0;top:536px;height:377px">
  <div class="offer-photo" style="top:10px;background:linear-gradient(90deg,#d8dadf,#eef0f3 45%,#3d63e6 75%,#dfe3ee)" role="img" aria-label="Ladestecker einer Wallbox mit blau leuchtendem Ring"></div>
  <div class="offer-banner" style="top:117px">ALS PRIVATKUNDE</div>
  <ul class="offer-list" style="top:162px">
    <li><svg><use href="#tick"/></svg>Bestandsanalyse mit umfangreicher Beratung über<br>die Möglichkeiten der Umsetzung</li>
    <li><svg><use href="#tick"/></svg>Prüfung und Übernahme der Anmeldung verfügbarer<br>Fördermöglichkeiten</li>
    <li><svg><use href="#tick"/></svg>Auswahl an smarten Wallbox Lösungen, passend für<br>Ihr Fahrzeug und Ihre Bedürfnisse</li>
    <li><svg><use href="#tick"/></svg>Installation inkl. aller notwendigen Materialien und<br>Tätigkeiten (Durchbrüche, Erdarbeiten, etc.)</li>
    <li><svg><use href="#tick"/></svg>Inbetriebnahme und Einweisung in die Ladetechnik</li>
    <li><svg><use href="#tick"/></svg>Jährlich technische Wartung nach DGUV3</li>
    <li><svg><use href="#tick"/></svg>Reparaturservice, unter Berücksichtigung der<br>geltenden Garantie Ansprüche</li>
  </ul>
</article>

<article class="offer" style="left:269px;top:505px;height:558px">
  <div class="offer-photo" style="top:11px;background:linear-gradient(120deg,#2b5fa8,#a9c6e3 40%,#e5edf5 65%,#7fa6d0)" role="img" aria-label="Ladekabel steckt in der Ladebuchse eines Elektroautos"></div>
  <div class="offer-banner is-business" style="top:118px">ALS GESCHÄFTSKUNDE</div>
  <ul class="offer-list" style="top:162px;width:252px">
    <li><svg><use href="#tick"/></svg>Durchführung einer individuellen Bedarfsanalyse inkl.<br>Ermittlung der Anforderungen für:</li>
    <li class="sub">Haus- und Immobilienverwaltungen</li>
    <li class="sub">Dienstleistungs- und Handelsunternehmen</li>
    <li class="sub">Hotel und Beherbergungsbetriebe</li>
    <li class="sub">Parkraum- und Parkhausbetreiber</li>
    <li class="sub">Tourismus, Sport- und Freizeiteinrichtungen</li>
    <li><svg><use href="#tick"/></svg>Planung und Projektierung des Installationsaufwands<br>inkl. Materialverbrauch</li>
    <li><svg><use href="#tick"/></svg>Leasing oder Kauf der Hardware</li>
    <li><svg><use href="#tick"/></svg>Normgerechte Installation der Ladeinfrastruktur inkl.<br>Durchbruch-, Brandschutz- und Erdarbeiten</li>
    <li><svg><use href="#tick"/></svg>Bei Bestandsbauten Integration der Ladeinfrastruktur in<br>die Gebäudesystemtechnik und ggf. Anpassung des<br>Netzanschlusses</li>
    <li><svg><use href="#tick"/></svg>Inbetriebnahme der Anlage inkl. Prüf- und<br>Messprotokollen</li>
    <li><svg><use href="#tick"/></svg>Wiederkehrende technische Prüfung der Anlage nach<br>DGUV 3</li>
    <li><svg><use href="#tick"/></svg>Austausch und Reparatur Service</li>
    <li><svg><use href="#tick"/></svg>Unterstützung bei der mtl. Nutzungsabrechnung und<br>Einbindung in Ihre vorhandene Abrechnungssysteme</li>
    <li><svg><use href="#tick"/></svg>ODER direkte Abrechnung mit den Nutzern</li>
  </ul>
</article>

<article class="offer" style="left:538px;top:536px;height:377px;width:256px">
  <div class="offer-photo" style="top:10px;background:linear-gradient(90deg,#3a5c8a,#8aa3c0 35%,#2a3140 70%,#1f3a8a)" role="img" aria-label="Öffentliche Ladesäule mit eingestecktem blauem Ladestecker"></div>
  <div class="offer-banner" style="top:117px">ALS KOMMUNE</div>
  <ul class="offer-list" style="top:162px">
    <li><svg><use href="#tick"/></svg>Konzeptionierung möglicher Ladeinfrastrukturen<br>innerhalb Ihrer Gemeinde</li>
    <li><svg><use href="#tick"/></svg>Planung und Projektsteuerung inkl. sämtlicher<br>behördlicher Genehmigungsverfahren und<br>Beantragung von Fördermitteln</li>
    <li><svg><use href="#tick"/></svg>Fachgerechte Installation und Inbetriebnahme</li>
    <li><svg><use href="#tick"/></svg>Regelmäßige Wartung gemäß Vorschrif</li>
    <li><svg><use href="#tick"/></svg>Reparatur und Kundenservice</li>
    <li><svg><use href="#tick"/></svg>Direkte Abrechnung mit dem Nutzer</li>
    <li><svg><use href="#tick"/></svg>Beteiligung der Gemeinde am Umsatz</li>
    <li><svg><use href="#tick"/></svg>Möglichkeit der Integration von Bonusprogrammen,<br>mit denen der lokale Einzelhandel beworben wird</li>
  </ul>
</article>

<footer class="site-footer">
  <span style="left:94px">©tanu-werk GmbH</span>
  <a style="left:253px">AGB</a>
  <a style="left:311px">Datenschutzerklärung</a>
  <a style="left:436px">Impressum</a>
  <a style="left:524px">Kontakt</a>
  <a style="left:598px">Karriere</a>
  <a style="left:674px">FAQs</a>
  <div class="social" style="left:95px"></div>
  <div class="social" style="left:128px"></div>
  <div class="social" style="left:162px"></div>
</footer>
</body>
</html>
```